Qarvesh Facilities Management brochure

to design suitable company brochure compatible with company scope work, ee are at Qarvesh handling all soft services such as housekeeping , landscaping, waste mangement and pest control and hard services such as building renovations and MEP maintenance ,,,,,,,,,,,,................nnnñnnnnnnnnnnnnnnnnnnnnnnnnnnnnnnnnnnnnnnmnñmmmmmmmmmmmmmmmmm

Target Market(s)

Saudi Arabia

Industry/Entity Type

Facilities Management

Font styles to use
Serif

Requirements
Must have
• Thems matching facilities management feild
Nice to have
• Innovation
Should not have
• Strangers faces photos

```html
<!DOCTYPE html>
<html lang="en">
<head>
<meta charset="utf-8">
<title>Qarvesh Facilities Management – Company Brochure</title>
<link rel="stylesheet" href="https://fonts.googleapis.com/css2?family=Lora:wght@400;500;600;700&display=swap">
<style>
:root{
  --orange:#F2A31F;
  --flame:#E5601D;
  --red:#A3282D;
  --navy:#1E4A6A;
  --ink:#2B2B2B;
  --grey:#5E5E5E;
  --canvas:#E8E8E8;
}
*{box-sizing:border-box;margin:0;padding:0}
html,body{width:1200px;height:4000px;overflow:hidden;background:var(--canvas)}
body{font-family:'Lora',serif;color:var(--ink)}
.brochure{width:1200px;height:4000px;display:flex;flex-direction:column;align-items:center;padding-top:34px;gap:34px}
.spread{width:656px;height:462px;display:flex;box-shadow:0 2px 8px rgba(0,0,0,.12);flex:none}
.page{width:328px;height:462px;position:relative;background:#fff;overflow:hidden}
.abs{position:absolute}
.ph{position:absolute;box-shadow:inset 0 0 0 1px rgba(0,0,0,.04)}
.title{position:absolute;left:30px;top:28px;font-size:10.5px;font-weight:500;color:var(--ink);line-height:1.2}
.title b{color:var(--red);font-weight:700}
.title .o{color:var(--flame);font-weight:700}
.body{font-size:5px;line-height:1.4;color:var(--grey)}
.label{position:absolute;left:30px;font-size:6px;font-weight:700;color:var(--flame);letter-spacing:.2px;white-space:nowrap}
.foot{position:absolute;bottom:24px;height:18px;display:flex;align-items:center}
.foot.l{left:30px;right:0}
.foot.r{left:0;right:30px}
.brand{font-size:10px;font-weight:700;color:var(--red);display:flex;align-items:center;gap:4px;white-space:nowrap}
.brand i{width:7px;height:7px;background:var(--flame);display:block}
.rule{flex:1;height:1px;background:var(--orange);position:relative;margin:0 6px}
.pill{position:absolute;top:-5px;left:50%;transform:translateX(-50%);background:var(--red);color:#fff;font-size:4.6px;padding:3px 9px;border-radius:6px;white-space:nowrap}
.dot{width:10px;height:10px;border-radius:50%;background:var(--orange);border:2px solid #fff;box-shadow:0 0 0 1px var(--orange);flex:none}
.cover-band{left:0;top:168px;width:328px;height:130px;background:var(--orange)}
.contact{position:absolute;left:0;width:328px;text-align:center}
.contact h4{font-size:8px;color:#fff;font-weight:700;letter-spacing:.5px}
.contact p{font-size:5px;line-height:1.35;color:#fff;font-weight:600}
.cicon{width:12px;height:12px;border-radius:50%;background:var(--flame);margin:4px auto 3px;display:flex;align-items:center;justify-content:center}
.cline{font-size:8.5px;font-weight:700;color:var(--ink)}
.tagline{position:absolute;right:26px;top:380px;text-align:right}
.tagline .a{font-size:18px;font-weight:400;letter-spacing:.5px;color:var(--ink)}
.tagline .b{font-size:18px;font-weight:700;color:var(--ink)}
.tagline .b span{color:var(--flame)}
.web{position:absolute;right:55px;top:436px;font-size:9px;letter-spacing:1px;color:var(--ink)}
.md-box{left:0;top:56px;width:222px;height:84px;background:var(--orange);padding:10px 50px 0 30px;color:#fff;font-size:5px;line-height:1.4}
.md-photo{left:200px;top:44px;width:100px;height:100px;border-radius:50%;border:4px solid #fff;background:linear-gradient(160deg,#e9e6e1 0%,#b7aea2 45%,#5f5a55 100%);box-shadow:0 1px 4px rgba(0,0,0,.25)}
.cols{position:absolute;display:flex;gap:12px}
.cols p{flex:1;text-align:justify}
.quote{position:absolute;font-size:30px;font-weight:700;color:var(--flame);line-height:1}
.lead{position:absolute;left:30px;top:84px;width:268px;font-size:6.2px;font-weight:700;line-height:1.35;color:var(--ink)}
.sub{position:absolute;left:30px;top:44px;font-size:4.6px;font-weight:700;color:var(--ink)}
.mvv{position:absolute;top:232px;width:84px;text-align:center}
.mvv .ic{width:42px;height:42px;border-radius:50%;background:#fff;border:2px solid var(--red);margin:0 auto -10px;position:relative;z-index:2;display:flex;align-items:center;justify-content:center}
.mvv .box{background:var(--red);color:#fff;padding:14px 6px 8px;height:115px;border-radius:3px}
.mvv.or .box{background:var(--orange)}
.mvv h5{font-size:8.5px;font-weight:600;margin-bottom:3px}
.mvv p{font-size:5px;line-height:1.35}
.qbox{left:86px;top:152px;width:216px;height:72px;background:var(--red);color:#fff;padding:14px 16px 0 30px;font-size:5px;line-height:1.4}
.stat{position:absolute;display:flex;align-items:center;gap:8px}
.stat .n{font-size:10px;font-weight:600;color:var(--red);line-height:1}
.stat .s{font-size:5.5px;color:var(--grey)}
.seg-red{left:145px;top:0;width:183px;height:462px;background:var(--red)}
.seg-row{position:absolute;left:30px;height:32px;display:flex;align-items:center}
.seg-img{width:140px;height:32px;border-radius:0 16px 16px 0}
.seg-ic{position:absolute;left:146px;top:8px;width:16px;height:16px;border-radius:50%;background:var(--orange);border:2px solid #fff}
.seg-txt{position:absolute;left:172px;top:10px;font-size:8.5px;font-weight:700;color:#fff;letter-spacing:.3px;white-space:nowrap}
.ifm{position:absolute;display:flex;align-items:center;gap:8px;font-size:6px;font-weight:600;color:var(--ink);line-height:1.25}
.so-left{background:linear-gradient(135deg,#a3282d 0%,#8d2226 55%,#a6383b 100%)}
.so-title{position:absolute;left:84px;top:186px;font-size:26px;line-height:1.1;font-weight:500;color:#fff}
.so-title span{color:var(--orange);display:block}
.navy-box{left:46px;top:132px;width:250px;height:134px;background:var(--navy);display:flex;gap:12px;padding:12px}
.navy-box .body{color:#e9eef3;font-size:4.8px}
.navy-box ul{list-style:none;flex:1}
.navy-box li{font-size:4.8px;color:#e9eef3;margin-bottom:7px;padding-left:7px;position:relative}
.navy-box li:before{content:"";position:absolute;left:0;top:1px;border-left:3px solid var(--orange);border-top:2px solid transparent;border-bottom:2px solid transparent}
.card{position:absolute;left:30px;width:268px;height:100px;display:flex}
.card .img{width:120px;height:100%}
.card .txt{flex:1;padding:10px 14px;color:#fff;font-size:5px;line-height:1.4}
.card .or{background:var(--orange)}
.card .rd{background:var(--red)}
.list-box{left:18px;top:30px;width:264px;height:192px;background:var(--navy);padding:12px 16px}
.list-box li{list-style:none;font-size:5.6px;color:#fff;display:flex;align-items:center;gap:9px;height:14.5px;border-bottom:1px solid rgba(255,255,255,.08)}
.list-box li i{width:7px;height:7px;border:1.2px solid #fff;transform:rotate(45deg);display:block}
.kpis{left:18px;top:340px;width:264px;height:56px;display:flex}
.kpis div{flex:1;color:#fff;padding:8px 6px;font-size:4.6px;line-height:1.3}
.kpis b{display:block;font-size:13px;font-weight:600;line-height:1.1;margin-bottom:3px}
.kpis b.sm{font-size:5px;font-weight:700}
</style>
</head>
<body>
<main class="brochure">

<section class="spread">
  <div class="page">
    <div class="ph" style="left:40px;top:18px;width:245px;height:168px;background:linear-gradient(180deg,#ffffff 0%,#cfdbe6 18%,#7d93ab 45%,#3f536b 72%,#8f3236 100%);z-index:2" role="img" aria-label="Photo of the company headquarters building"></div>
    <div class="abs cover-band"></div>
    <div class="contact" style="top:198px">
      <h4>CONTACT US</h4>
      <div class="cicon"><svg width="6" height="7" viewBox="0 0 6 7"><path d="M3 0a2.5 2.5 0 0 0-2.5 2.5C.5 4.3 3 7 3 7s2.5-2.7 2.5-4.5A2.5 2.5 0 0 0 3 0z" fill="#fff"/></svg></div>
      <p>Qarvesh Facilities Management<br>Trading Co. LLC,<br>Al Noor Business Street,<br>Al Khobar,<br>Eastern Province,<br>Kingdom of Saudi Arabia</p>
    </div>
    <div class="contact" style="top:310px">
      <div class="cicon"><svg width="6" height="6" viewBox="0 0 6 6"><path d="M1 0l1.3 1.6-.7.8c.4.8 1 1.4 1.8 1.8l.8-.7L6 4.8 5 6C2.4 5.7.3 3.6 0 1z" fill="#fff"/></svg></div>
      <div class="cline">+966 3 555 0142</div>
      <div class="cicon"><svg width="7" height="5" viewBox="0 0 7 5"><rect width="7" height="5" fill="#fff"/><path d="M0 0l3.5 2.7L7 0" stroke="#E5601D" stroke-width=".8" fill="none"/></svg></div>
      <div class="cline">info@qarvesh.com</div>
      <div class="cicon"><svg width="7" height="7" viewBox="0 0 7 7"><circle cx="3.5" cy="3.5" r="3" stroke="#fff" fill="none"/><path d="M.5 3.5h6M3.5.5v6" stroke="#fff" stroke-width=".6"/></svg></div>
      <div class="cline">www.qarvesh.com</div>
    </div>
    <div class="brand abs" style="left:82px;top:424px"><i></i>Qarvesh</div>
    <div class="abs" style="left:196px;top:418px;width:48px;height:26px;border-radius:3px;background:#d6d6d6"></div>
  </div>
  <div class="page">
    <div class="brand abs" style="right:42px;top:30px;font-size:14px"><i style="width:10px;height:10px"></i>Qarvesh</div>
    <div class="ph" style="left:40px;top:84px;width:260px;height:260px;border-radius:50%;background:linear-gradient(150deg,#f2a31f 0%,#e5601d 40%,#7a3324 75%,#3a2a26 100%);border:6px solid #e5601d" role="img" aria-label="Round collage of facility and workplace photos"></div>
    <div class="tagline"><div class="a">YOUR SUCCESS</div><div class="b">IS OUR <span>PRIMARY GOAL.</span></div></div>
    <div class="web">www.<b>qarvesh</b>.com</div>
  </div>
</section>

<section class="spread">
  <div class="page">
    <div class="title">Message From <b>Managing Director</b></div>
    <div class="abs md-box">It gives me great pleasure to welcome you to Qarvesh. Here you will find a brief review of our company, reflecting the pride of our people and the values that guide our work. It also conveys our sense of mission and vision to become the preferred partner in facilities management.</div>
    <div class="ph md-photo" role="img" aria-label="Portrait of the managing director"></div>
    <div class="cols body" style="left:30px;top:176px;width:268px">
      <p>Today, change is everywhere. Our customers' markets are evolving rapidly in response to new technology, new service trends and rising expectations. There is a growing demand for better, cleaner and more efficient services and ways of performing them. Companies that prepare for these changes will see real potential in the challenges ahead. Since our foundation, Qarvesh has sought to adapt quickly to customer needs and market requirements. Our tradition of ingenuity has driven steady improvement in the way we operate as a partner for sustainable growth. We are taking full advantage of the latest wave of change, and we are equipping our teams with the skills, tools and systems they need to meet new demands in technical, soft and hygiene services across every sector we serve.</p>
      <p>This transformation aims at making us more agile, cost efficient and aligning us ever more closely to the needs and requirements of our customers. A growing world needs cost effective, more efficient services, while at the same time meeting high safety standards. It needs innovation and technical work forces with whom we continuously train them to be able to face new challenges and improve our quality of life. Here you will also discover our commitment to the communities where we live and work, how we protect and sustain the environment we all share, and our pioneering technology that builds a better future. Our high quality products are offered to our customers and the shareholders that trust us. We call this the chemistry that matters.</p>
    </div>
    <div class="foot l"><div class="brand"><i></i>Qarvesh</div><div class="rule"><span class="pill">www.qarvesh.com</span></div><div class="dot"></div></div>
  </div>
  <div class="page">
    <div class="title">Our <b>Leadership Team</b></div>
    <div class="quote" style="left:30px;top:54px">“</div>
    <div class="lead">We strongly believe in long-term partnerships with a clear roadmap on benefits to our clients on cost, process, infrastructure enhancements and efficiency building. Our client retention since inception is a strong testimony of our service excellence and cost effectiveness.</div>
    <div class="quote" style="right:30px;top:124px">”</div>
    <div class="ph" style="left:46px;top:168px;width:236px;height:212px;border-radius:6px;background:linear-gradient(180deg,#fdf3df 0%,#f8d98f 45%,#f2a31f 75%,#1e4a6a 100%)" role="img" aria-label="Illustration of a team celebrating around a trophy"></div>
    <div class="foot r"><div class="dot"></div><div class="rule"><span class="pill">www.qarvesh.com</span></div><div class="brand"><i></i>Qarvesh</div></div>
  </div>
</section>

<section class="spread">
  <div class="page">
    <div class="title">Business <b class="o">Objective</b></div>
    <div class="sub">MARKET TRENDSETTER IN THE INDUSTRIAL SERVICES MANAGEMENT DOMAIN.</div>
    <div class="ph" style="left:32px;top:64px;width:264px;height:160px;border-radius:10px;background:linear-gradient(160deg,#e8dcc3 0%,#b08d5c 35%,#6b4a2c 70%,#3a2b20 100%)" role="img" aria-label="Photo of a modern office corridor with glass partitions"></div>
    <div class="mvv" style="left:37px"><div class="ic"><svg width="20" height="20" viewBox="0 0 20 20" fill="none" stroke="#A3282D" stroke-width="1.4"><circle cx="10" cy="10" r="8"/><circle cx="10" cy="10" r="4.5"/><circle cx="10" cy="10" r="1.2" fill="#A3282D"/></svg></div><div class="box"><h5>Mission</h5><p>To deliver best-in-class service offerings to our clients and partners to help them drive meaningful customer experience.</p></div></div>
    <div class="mvv" style="left:122px"><div class="ic"><svg width="20" height="20" viewBox="0 0 20 20" fill="none" stroke="#A3282D" stroke-width="1.4"><path d="M2 10s3-5 8-5 8 5 8 5-3 5-8 5-8-5-8-5z"/><circle cx="10" cy="10" r="2.5"/></svg></div><div class="box"><h5>Vision</h5><p>To be the market trendsetter in the industrial services management domain and build a brand name espousing the highest standards in service delivery.</p></div></div>
    <div class="mvv or" style="left:207px"><div class="ic"><svg width="20" height="20" viewBox="0 0 20 20" fill="none" stroke="#A3282D" stroke-width="1.4"><circle cx="7" cy="8" r="4"/><circle cx="13" cy="12" r="4"/></svg></div><div class="box"><h5>Value</h5><p>We believe in value-driven service delivery. We are committed to the quality and safety standards set by the industry and offer a safe place to work for our employees.</p></div></div>
    <div class="foot l"><div class="brand"><i></i>Qarvesh</div><div class="rule"><span class="pill">www.qarvesh.com</span></div><div class="dot"></div></div>
  </div>
  <div class="page">
    <div class="title">Qarvesh<br><b>Solutions Inspired</b></div>
    <div class="cols body" style="left:30px;top:64px;width:268px">
      <p>Qarvesh offers a comprehensive range of smart, innovative facilities management solutions that target cost effective, sustainable results at the clients' facilities and workplaces. Our offerings include technical solutions, soft services, pest management, security and business support.</p>
      <p>Our solutions and specialised services are delivered across a variety of sectors and clients. At Qarvesh we combine a large pool of trained resources and industry expertise to meet the requirements of our clients, who come from diverse business sectors.</p>
    </div>
    <div class="abs qbox">We seek to add value to our customers by reducing their operational costs, mitigating risks and enabling them to augment their productivity.</div>
    <div class="abs" style="left:62px;top:162px;width:34px;height:34px;border-radius:50%;background:#fff;display:flex;align-items:center;justify-content:center"><svg width="20" height="24" viewBox="0 0 20 24"><circle cx="10" cy="9" r="8" fill="#F7C623"/><rect x="6" y="17" width="8" height="5" rx="1" fill="#9a9a9a"/></svg></div>
    <div class="quote" style="left:100px;top:156px;font-size:20px;color:var(--orange)">“</div>
    <div class="quote" style="right:34px;top:202px;font-size:20px;color:var(--orange)">”</div>
    <div class="body abs" style="left:30px;top:234px;width:268px">We at Qarvesh are driven to provide our clients with compelling value-based solutions through our comprehensive services management approach and benchmarking to create workspaces built on our cherished principles of quality, trust and service excellence. Our ISO 9001 certification is a testament to our quest for quality, safety and environmental sustainability.</div>
    <div class="stat" style="left:30px;top:276px"><svg width="30" height="22" viewBox="0 0 30 22" fill="none" stroke="#E5601D" stroke-width="1.3"><circle cx="8" cy="6" r="3"/><circle cx="22" cy="6" r="3"/><circle cx="15" cy="9" r="3"/><path d="M2 20c0-5 12-5 12 0M16 20c0-5 12-5 12 0"/></svg><div><div class="s">Over</div><div class="n">78 YEARS</div><div class="s">of expertise</div></div></div>
    <div class="abs" style="left:164px;top:272px;width:1px;height:96px;background:#ddd"></div>
    <div class="stat" style="left:176px;top:280px"><svg width="28" height="22" viewBox="0 0 28 22" fill="none" stroke="#E5601D" stroke-width="1.3"><rect x="2" y="6" width="10" height="14"/><rect x="15" y="2" width="11" height="18"/></svg><div><div class="n">20+ CLIENT</div><div class="s">locations/sites</div></div></div>
    <div class="stat" style="left:30px;top:330px"><svg width="30" height="22" viewBox="0 0 30 22" fill="none" stroke="#E5601D" stroke-width="1.3"><circle cx="15" cy="6" r="4"/><path d="M6 21c0-7 18-7 18 0"/></svg><div><div class="n">4000+</div><div class="s">Employees</div></div></div>
    <div class="stat" style="left:176px;top:330px"><svg width="28" height="22" viewBox="0 0 28 22" fill="none" stroke="#E5601D" stroke-width="1.3"><circle cx="14" cy="6" r="4"/><path d="M6 21c0-7 16-7 16 0"/></svg><div><div class="n">11+</div><div class="s">Clients</div></div></div>
    <div class="foot r"><div class="dot"></div><div class="rule"><span class="pill">www.qarvesh.com</span></div><div class="brand"><i></i>Qarvesh</div></div>
  </div>
</section>

<section class="spread">
  <div class="page">
    <div class="abs seg-red"></div>
    <div class="title">Business<br><b>Segments</b></div>
    <div class="seg-row" style="top:64px"><div class="ph seg-img" style="position:static;background:linear-gradient(90deg,#8fd0c5,#2f7f74)" role="img" aria-label="Healthcare photo"></div><span class="seg-ic"></span><span class="seg-txt">HEALTHCARE</span></div>
    <div class="seg-row" style="top:105px"><div class="ph seg-img" style="position:static;background:linear-gradient(90deg,#a9c6df,#2d5a84)" role="img" aria-label="Commercial buildings photo"></div><span class="seg-ic"></span><span class="seg-txt">COMMERCIAL</span></div>
    <div class="seg-row" style="top:146px"><div class="ph seg-img" style="position:static;background:linear-gradient(90deg,#7fc2cc,#1f5e6e)" role="img" aria-label="Infrastructure photo"></div><span class="seg-ic"></span><span class="seg-txt">INFRASTRUCTURE</span></div>
    <div class="seg-row" style="top:187px"><div class="ph seg-img" style="position:static;background:linear-gradient(90deg,#d9d6d0,#6f6a63)" role="img" aria-label="Government office photo"></div><span class="seg-ic"></span><span class="seg-txt">GOVERNMENT</span></div>
    <div class="seg-row" style="top:228px"><div class="ph seg-img" style="position:static;background:linear-gradient(90deg,#c3d0da,#56697a)" role="img" aria-label="Residential building photo"></div><span class="seg-ic"></span><span class="seg-txt">RESIDENTIAL</span></div>
    <div class="seg-row" style="top:269px"><div class="ph seg-img" style="position:static;background:linear-gradient(90deg,#b2cca9,#3e6137)" role="img" aria-label="Education campus photo"></div><span class="seg-ic"></span><span class="seg-txt">EDUCATION</span></div>
    <div class="seg-row" style="top:310px"><div class="ph seg-img" style="position:static;background:linear-gradient(90deg,#cfd6db,#545f69)" role="img" aria-label="Aviation photo"></div><span class="seg-ic"></span><span class="seg-txt">AVIATION</span></div>
    <div class="seg-row" style="top:351px"><div class="ph seg-img" style="position:static;background:linear-gradient(90deg,#b5c6dc,#2a4a78)" role="img" aria-label="Oil and gas facility photo"></div><span class="seg-ic"></span><span class="seg-txt">OIL &amp; GAS</span></div>
    <div class="foot l"><div class="brand"><i></i>Qarvesh</div><div class="rule" style="background:#fff"><span class="pill" style="background:transparent;color:#fff">www.qarvesh.com</span></div><div class="dot"></div></div>
  </div>
  <div class="page">
    <div class="title">Integrated Facility<br><b>Management</b></div>
    <div class="body abs" style="left:30px;top:68px;width:262px">The Need For Professional Integrated Facilities Management Services (IFM) Has Become A Necessity. A Well Maintained Facility Leads To A Healthy, Comfortable And Secure Work Environment, Where Maintenance Costs Are Optimised, Superior Quality Is Maintained And Management Systems And Processes Are Standardised.</div>
    <div class="body abs" style="left:30px;top:116px;width:262px">Qarvesh integrates processes and systems within an organisation to develop and maintain required services that support and enhance the effectiveness of our solutions. Our facility management is continuously re-defined and re-engineered for high quality results and contributes to the clients' bottom line. It encompasses all critical aspects ranging from technical and soft solutions to security management.</div>
    <div class="ifm" style="left:40px;top:220px"><svg width="30" height="30" viewBox="0 0 30 30" fill="none" stroke="#E5601D" stroke-width="1.4"><circle cx="15" cy="15" r="6"/><path d="M15 3v5M15 22v5M3 15h5M22 15h5M7 7l3 3M20 20l3 3M23 7l-3 3M7 23l3-3"/></svg>TECHNICAL<br>SOLUTIONS</div>
    <div class="ifm" style="left:176px;top:220px"><svg width="30" height="30" viewBox="0 0 30 30" fill="none" stroke="#A3282D" stroke-width="1.4"><path d="M15 4c4 6 7 9 7 13a7 7 0 0 1-14 0c0-4 3-7 7-13z"/><path d="M4 26h22"/></svg>HYGIENE &amp;<br>SOFT SERVICE<br>SOLUTIONS</div>
    <div class="ifm" style="left:40px;top:290px"><svg width="30" height="30" viewBox="0 0 30 30" fill="none" stroke="#E5601D" stroke-width="1.4"><circle cx="15" cy="11" r="7"/><path d="M11 18l-3 9 7-3 7 3-3-9"/></svg>SPECIALISED<br>SERVICE<br>SOLUTION</div>
    <div class="ifm" style="left:176px;top:290px"><svg width="30" height="30" viewBox="0 0 30 30" fill="none" stroke="#A3282D" stroke-width="1.4"><circle cx="12" cy="9" r="4"/><path d="M4 26c0-8 16-8 16 0"/><rect x="18" y="14" width="9" height="11"/></svg>PROJECTS<br>SUPPORT<br>SERVICES</div>
    <div class="foot r"><div class="dot"></div><div class="rule"><span class="pill">www.qarvesh.com</span></div><div class="brand"><i></i>Qarvesh</div></div>
  </div>
</section>

<section class="spread">
  <div class="page so-left" role="img" aria-label="Red panel over a faint construction crane photo">
    <div class="so-title">OUR<span>SERVICE<br>OFFERINGS</span></div>
    <div class="foot l"><div class="brand" style="color:#fff"><i></i>Qarvesh</div><div class="rule" style="background:rgba(255,255,255,.5)"><span class="pill" style="background:transparent">www.qarvesh.com</span></div><div class="dot"></div></div>
  </div>
  <div class="page">
    <div class="title">Technical <b>Solutions</b></div>
    <div class="abs" style="left:30px;top:54px;width:270px;font-size:7.2px;line-height:1.3;color:var(--ink)">We are modernising the facilities and workplaces through innovation and providing valuable services.</div>
    <div class="abs" style="left:30px;top:88px;font-size:6.4px;font-weight:700;line-height:1.3">Electro-Mechanical Services<br>&amp; Building Repairs</div>
    <div class="abs navy-box">
      <div class="body" style="flex:1.1">From capital asset and facility maintenance to managing MEP services and building fabric, our highly trained maintenance professionals take care of the day-to-day jobs that keep facilities and assets performing optimally.<br><br><span style="color:var(--orange)">These include:</span> Our zero tolerance for unplanned downtime is backed by our reliability of assured maintenance programme and our computer aided facility management system (CAFM) tools for anticipating and avoiding equipment failure that could otherwise lead to productivity loss.</div>
      <ul><li>Building Construction</li><li>Building and community housing maintenance</li><li>HVAC Operations and Maintenance</li><li>Electrical Operations and Maintenance</li><li>STP / WTP Maintenance</li><li>Building renovation and Maintenance</li><li>Water proofing</li></ul>
    </div>
    <div class="ph" style="left:0;top:300px;width:328px;height:162px;background:linear-gradient(180deg,#9fc3e3 0%,#c7d9ea 30%,#e3d8c4 50%,#b39d7c 70%,#6f6453 100%)" role="img" aria-label="Photo of a residential villa complex"></div>
    <div class="foot r"><div class="dot"></div><div class="rule" style="background:#fff"><span class="pill">www.qarvesh.com</span></div><div class="brand" style="color:#fff"><i></i>Qarvesh</div></div>
  </div>
</section>

<section class="spread">
  <div class="page">
    <div class="title">Hygiene &amp; <b class="o">Soft Services</b></div>
    <div class="label" style="top:76px">GENERAL CLEANING SERVICES</div>
    <div class="card" style="top:90px"><div class="img ph" style="position:static;background:linear-gradient(135deg,#d9cfb9,#a9843a 60%,#6b5630)" role="img" aria-label="Photo of a wet floor caution sign and cleaning equipment"></div><div class="txt or">Our efficient and highly trained staff uses environment friendly products and adopts to industry's best practices in order to consistently deliver results that exceed client's expectations. Our cleaning services are in full compliance with BICSc standard practices.</div></div>
    <div class="label" style="top:234px">PANTRY SERVICES</div>
    <div class="card" style="top:248px"><div class="txt rd">Our efficient and highly trained staff uses environment friendly products and adopts to industry's best practices in order to consistently deliver results that exceed client's expectations. Our cleaning services are in full compliance with BICSc standard practices.</div><div class="img ph" style="position:static;background:linear-gradient(135deg,#d64a3a,#e9c99a 55%,#8fb2cf)" role="img" aria-label="Photo of a grocery bag for pantry supplies"></div></div>
    <div class="foot l"><div class="brand"><i></i>Qarvesh</div><div class="rule"><span class="pill">www.qarvesh.com</span></div><div class="dot"></div></div>
  </div>
  <div class="page">
    <div class="title">Hygiene &amp; <b class="o">Soft Services</b></div>
    <div class="label" style="top:76px">PEST CONTROL SERVICES</div>
    <div class="card" style="top:90px"><div class="img ph" style="position:static;background:linear-gradient(135deg,#f0f3f6,#9fb2c3 55%,#4f6578)" role="img" aria-label="Photo of a pest control technician in protective suit"></div><div class="txt or">Our pest control services uses environment friendly products to protect your premises ensuring that it meets the appropriate quality, health and safety regulations.<br>• General Disinfestation Services<br>• Cockroach, Rodent, Mosquito and Bird Management<br>• Termite and Wood Borer Management<br>• Bedbug Treatment</div></div>
    <div class="label" style="top:234px">LANDSCAPING SERVICES &amp; GARDENING SERVICES</div>
    <div class="card" style="top:248px"><div class="txt rd">Our efficient and highly trained staff uses environment friendly products and adopts to industry's best practices in order to consistently deliver results that exceed client's expectations. Our cleaning services are in full compliance with BICSc standard practices.</div><div class="img ph" style="position:static;background:linear-gradient(135deg,#a7c98a,#4f7a35 55%,#2d4a20)" role="img" aria-label="Photo of lawn mowing and garden care"></div></div>
    <div class="foot r"><div class="dot"></div><div class="rule"><span class="pill">www.qarvesh.com</span></div><div class="brand"><i></i>Qarvesh</div></div>
  </div>
</section>

<section class="spread">
  <div class="page">
    <div class="title">Specialised <b class="o">Service Solutions</b></div>
    <div class="label" style="top:70px">EIFS SERVICE</div>
    <div class="card" style="top:84px"><div class="img ph" style="position:static;background:linear-gradient(135deg,#ebe6dd,#9a8c78 55%,#4e463d)" role="img" aria-label="Photo of workers applying exterior wall insulation"></div><div class="txt or">Exterior Insulation and Finish System (EIFS) is an exterior wall cladding that utilizes rigid insulation boards on the exterior of the wall sheathing with a plaster appearance exterior skin. EIFS is the best performing cladding in relation to thermal and moisture control when compared to brick, stucco and conventional fiberboard siding.</div></div>
    <div class="label" style="top:234px">FAÇADE CLEANING SERVICES</div>
    <div class="card" style="top:248px"><div class="txt rd" style="padding-top:22px">We have experienced and competent workforce to carry out Façade Cleaning services to ensure the building façade is free of dust, grime and rain smear and marks.</div><div class="img ph" style="position:static;background:linear-gradient(135deg,#a9cbe8,#2e5f8c 55%,#17324d)" role="img" aria-label="Photo of rope access workers cleaning a glass facade"></div></div>
    <div class="foot l"><div class="brand"><i></i>Qarvesh</div><div class="rule"><span class="pill">www.qarvesh.com</span></div><div class="dot"></div></div>
  </div>
  <div class="page">
    <div class="label" style="top:32px">WASTE MANAGEMENT SOLUTIONS</div>
    <div class="card" style="top:44px;height:98px"><div class="img ph" style="position:static;background:linear-gradient(135deg,#f1d35a,#c69a1f 55%,#5d6b3a)" role="img" aria-label="Photo of a waste collection truck"></div><div class="txt or" style="padding-top:18px">We at Qarvesh offer exceptional waste management and recycling services. Our waste management and recycling solutions covering all types of waste lines.</div></div>
    <div class="label" style="top:158px">OIL &amp; GAS TRADING</div>
    <div class="card" style="top:170px;height:96px"><div class="txt rd" style="padding-top:26px">Oil &amp; Gas Maintenance Equipment's Trading Wellhead maintenance (WHM) (Routine &amp; Non-routine)</div><div class="img ph" style="position:static;background:linear-gradient(135deg,#e0e4e8,#e5601d 45%,#4a525c)" role="img" aria-label="Photo of an engineer at an oil and gas site"></div></div>
    <div class="label" style="top:280px">WASTE MANAGEMENT SOLUTIONS</div>
    <div class="card" style="top:292px;height:100px"><div class="img ph" style="position:static;background:linear-gradient(135deg,#eef4f9,#7ea3c4 55%,#2f5a82)" role="img" aria-label="Photo of a technician checking energy equipment"></div><div class="txt or" style="padding-top:18px">Our subject matter experts in energy efficiency help reduce energy utility bills and carbon emissions through a wide spectrum of cost-effective strategies.</div></div>
    <div class="foot r"><div class="dot"></div><div class="rule"><span class="pill">www.qarvesh.com</span></div><div class="brand"><i></i>Qarvesh</div></div>
  </div>
</section>

<section class="spread">
  <div class="page">
    <div class="title">Project <b class="o">Support Services</b></div>
    <div class="body abs" style="left:30px;top:50px;width:268px">Qarvesh has more than two decades of experience in providing services of professional workforce across wide range of disciplines to reputed clients in KSA. Our presence in all over Saudi Arabia, professional team with industrial background and such vast experience of 75+ years in services industry makes us stand out bright among others in the market. Our Project Support Services Division specializes in provision of tradesmen to meet your project's needs in these critical disciplines.</div>
    <div class="ph" style="left:0;top:130px;width:328px;height:256px;background:linear-gradient(180deg,#f4f4f2 0%,#dcdcda 40%,#a9a8a6 75%,#6b6a69 100%)" role="img" aria-label="Photo of a project team meeting around a whiteboard"></div>
    <div class="foot l"><div class="brand"><i></i>Qarvesh</div><div class="rule"><span class="pill">www.qarvesh.com</span></div><div class="dot"></div></div>
  </div>
  <div class="page">
    <ul class="abs list-box">
      <li><i></i>Project Engineers</li>
      <li><i></i>Certified Scaffold Supervisors /Inspectors</li>
      <li><i></i>Certified Rigging Workforce</li>
      <li><i></i>Accredited Health &amp; Safety Professionals</li>
      <li><i></i>Certified PTW/WPR professional</li>
      <li><i></i>Qualified Technicians (Elect/Inst/Mech)</li>
      <li><i></i>Certified QA/QC Professionals</li>
      <li><i></i>Certified Multi Welders</li>
      <li><i></i>Certified Crews for Piping works (Fabricators/Fitters)</li>
      <li><i></i>Administrative Staff</li>
      <li><i></i>Manufacturing Operators</li>
    </ul>
    <div class="abs kpis">
      <div style="background:var(--orange)"><b>4000+</b>Motivated Employees</div>
      <div style="background:var(--red)"><b class="sm">DAILY REPORTS ON CLIENT PRODUCTIVITY</b>Daily Reports</div>
      <div style="background:var(--red)"><b class="sm">BUSINESS ACUMEN</b>(75+ years in Business)</div>
      <div style="background:var(--orange)"><b>24 / 7</b>Support Service</div>
    </div>
    <div class="foot r"><div class="dot"></div><div class="rule"><span class="pill">www.qarvesh.com</span></div><div class="brand"><i></i>Qarvesh</div></div>
  </div>
</section>

</main>
</body>
</html>
```